Electric mountain bike tours nz

We are an Electric Mountain bike tour company in New Zealand. We will be offering bike rental and guided tours around the Nelson region in New Zealand. I want our website to represent both Mountain biking and New Zealand with the colours layout and features. We want tabs for the following:
-1 about us
-2 what we offer
-3 bookings/contact
Under the about us tab will be who we are as a a company. I want the ability to add videos to each of these tabs as we move foward with videos of the tracks we will be riding. I want the website to be editable so I can add and remove videos/photos myself. Also "our bikes" will be under this tab.
Under the what we offer tab will be
-1 bike rental and pricing
-2 guided tours and pricing
-3 recommended package deals.
I want to able to put the tracks under the guided tours tab and select beginner/ intermediate/advanced and have the tracks in each of the following to match the rider level. Also to be able to have a small video of the track would be great in this section.
Bookings and contact tab
(Further information for this tab to be updated soon)
Coded - Design and coding required
1 page
- Silver ferns, kiwi, mountains

```html
<!DOCTYPE html>
<html lang="en">
<head>
<meta charset="utf-8">
<title>RIDGEFERN — Electric Mountain Bike Tours</title>
<link href="https://fonts.googleapis.com/css2?family=Lato:wght@300;400;700;900&display=swap" rel="stylesheet">
<style>
:root{
  --ink:#111;
  --text:#444;
  --muted:#888;
  --white:#fff;
  --grey-band:#e2e2e2;
  --green:#3ea536;
  --green-dark:#2f8a29;
  --footer:#0b0b0b;
  --bottom:#2b2b2b;
  --hero-a:#5b6b4a;
  --hero-b:#8a8f6a;
  --offer-a:#2e2a24;
  --offer-b:#4a4236;
  --sky:#6f8fa8;
  --blue:#2d6fa3;
}
*{box-sizing:border-box;margin:0;padding:0}
html,body{width:1200px;height:4156px;overflow:hidden}
body{font-family:'Lato',sans-serif;color:var(--text);background:var(--white);position:relative}
section,header,footer{position:absolute;left:0;width:1200px}
.photo{display:block}
.center{text-align:center}
.title{font-family:'Lato',sans-serif;font-weight:700;font-size:40px;color:var(--ink);text-align:center}
.title .light{font-weight:300;color:var(--muted)}
.lorem{font-size:15px;line-height:24px;color:var(--text);text-align:center}
.btn{display:inline-flex;align-items:center;background:var(--ink);color:var(--white);font-size:13px;font-weight:700;letter-spacing:1px;height:32px;padding:0 0 0 14px}
.btn .arr{display:flex;align-items:center;justify-content:center;width:32px;height:32px;margin-left:10px}
.arrow-side{position:absolute;width:30px;height:50px}

/* header */
.site-header{top:0;height:140px;background:var(--white)}
.brand{position:absolute;left:76px;top:36px;display:flex;align-items:center;gap:12px;font-size:28px;font-weight:900;color:var(--ink)}
.brand .dot{width:56px;height:56px;border-radius:50%;background:var(--ink)}
.contact-top{position:absolute;right:88px;top:40px;display:flex;gap:28px;font-size:14px;color:var(--ink);font-weight:700}
.contact-top span{display:flex;align-items:center;gap:6px}
.nav{position:absolute;right:88px;top:80px;display:flex;gap:46px;font-size:14px;font-weight:700;color:var(--ink)}
.nav a{text-decoration:none;color:inherit;padding-bottom:6px}
.nav a.active{color:var(--muted);border-bottom:2px solid var(--green)}

/* hero */
.hero{top:140px;height:592px}
.hero .photo{position:absolute;inset:0;background:linear-gradient(180deg,#7d8c9a 0%,var(--hero-b) 35%,var(--hero-a) 70%,#3f4a33 100%)}
.hero .content{position:absolute;top:240px;width:100%;text-align:center;color:var(--white)}
.hero h1{font-size:60px;font-weight:900;letter-spacing:2px}
.hero p{font-size:17px;line-height:24px;margin-top:14px}
.hero .btn{margin-top:28px}

/* about */
.about{top:732px;height:628px}
.about .title{margin-top:62px}
.subtitle{font-size:15px;line-height:22px;color:var(--muted);text-align:center;margin-top:10px}
.gallery{display:flex;gap:18px;justify-content:center;margin-top:40px}
.gallery .photo{width:290px;height:172px}
.gallery .photo:first-child{outline:4px solid var(--green);outline-offset:-4px}
.about .lorem{width:920px;margin:30px auto 0}
.about .btn,.bike .btn{margin-top:28px}

/* bike */
.bike{top:1360px;height:420px;background:var(--grey-band)}
.bike .title{margin-top:94px}
.bike .lorem{width:920px;margin:22px auto 0}

/* offer */
.offer{top:1780px;height:720px}
.offer>.photo{position:absolute;inset:0;background:linear-gradient(160deg,var(--offer-b),var(--offer-a) 60%,#1c1a16)}
.offer .title{position:relative;margin-top:60px;color:var(--white)}
.offer .title .light{color:#cfcfcf}
.offer .intro{position:relative;width:820px;margin:12px auto 0;font-size:15px;line-height:22px;color:#e8e8e8;text-align:center}
.cards{position:absolute;left:140px;display:flex;gap:32px}
.card{width:280px;background:var(--white);text-align:center;box-shadow:0 4px 14px rgba(0,0,0,.25)}
.offer .cards{top:220px}
.card .photo{height:240px}
.card h3{font-size:16px;font-weight:700;color:var(--ink);margin-top:20px}
.card .date{font-size:13px;color:var(--muted);margin-top:4px}
.card p{font-size:12px;line-height:18px;color:var(--text);padding:8px 22px 0}
.card .btn{margin:16px 0 22px;transform:scale(.9)}
.offer .card{height:428px}
.offer .card .photo{border:4px solid var(--white)}

/* blog */
.blog{top:2500px;height:640px;background:linear-gradient(180deg,#d2d2d2,#ececec 50%,#d6d6d6)}
.blog .title{margin-top:42px}
.blog .cards{top:128px}
.blog .card{height:440px}
.blog .card .photo{height:252px}

/* testimonials */
.testi{top:3140px;height:380px}
.testi h2{position:absolute;top:78px;font-size:28px;font-weight:700;color:var(--ink)}
.testi h2 .light{font-weight:300;color:var(--muted)}
.testi h2.t1{left:280px}
.testi h2.t2{left:680px}
.testi h2.t2 .light{color:var(--blue);font-weight:700}
.quote{position:absolute;left:140px;top:152px;width:440px;height:192px;border:2px solid #bbb;border-radius:4px;padding:34px 26px 0 30px}
.quote p{font-size:13px;line-height:19px;color:var(--text)}
.quote .who{position:absolute;right:24px;bottom:14px;font-size:13px;font-weight:700;color:var(--ink)}
.avatar{position:absolute;left:160px;top:112px;width:70px;height:70px;border-radius:50%;background:#c9c2b8;border:3px solid var(--white);box-shadow:0 0 0 2px #bbb}
.video{position:absolute;left:672px;top:148px;width:400px;height:200px}
.video .photo{position:absolute;inset:0;background:linear-gradient(135deg,#3d5561,#6b8a72 55%,#2f3a2e)}
.video .bar{position:absolute;left:0;right:0;bottom:0;height:26px;background:rgba(0,0,0,.7)}

/* newsletter */
.news{top:3520px;height:100px;background:var(--green)}
.news .icon{position:absolute;left:186px;top:28px;width:44px;height:44px;border-radius:50%;background:var(--white)}
.news .label{position:absolute;left:244px;top:33px;font-size:26px;line-height:34px;font-weight:400;color:var(--white);white-space:nowrap}
.news .input{position:absolute;left:532px;top:31px;width:380px;height:38px;background:var(--white);font-size:13px;color:var(--muted);padding:11px 12px}
.news .sub{position:absolute;left:940px;top:31px;width:230px;height:38px;background:var(--ink);color:var(--white);font-size:14px;font-weight:700;letter-spacing:1px;text-align:center;line-height:38px}

/* footer */
.site-footer{top:3620px;height:480px;background:var(--footer);color:#d8d8d8}
.f-brand{position:absolute;left:100px;top:70px;display:flex;flex-direction:column;align-items:center;gap:14px;font-size:30px;font-weight:900;color:var(--white)}
.f-brand .dot{width:120px;height:120px;border-radius:50%;background:var(--green)}
.follow{position:absolute;left:112px;top:350px;font-size:15px;font-weight:700;color:var(--white)}
.follow .row{display:flex;gap:10px;margin-top:14px}
.follow .row i{width:24px;height:24px;border-radius:50%;background:var(--white)}
.f-col h4{font-size:19px;font-weight:700;color:var(--white);padding-bottom:10px;border-bottom:1px solid #444;margin-bottom:14px}
.contact-col{position:absolute;left:372px;top:60px;width:230px;font-size:13px;line-height:22px}
.contact-col .item{display:flex;align-items:center;gap:8px}
.contact-col h4.ql{margin-top:26px}
.contact-col ul{list-style:none}
.contact-col li:before{content:"›";color:var(--green);margin-right:8px;font-weight:700}
.booking{position:absolute;left:652px;top:60px;width:548px}
.booking h4{border:none;margin-bottom:26px}
.form{display:grid;grid-template-columns:258px 258px;gap:14px 14px}
.field{height:30px;border:1px solid #777;font-size:12px;color:#bbb;padding:7px 8px;background:#111}
.field.msg{grid-column:1/3;height:96px}
.submit{display:inline-block;margin-top:14px;background:var(--green);color:var(--white);font-size:13px;font-weight:700;padding:8px 26px}
.bottom{top:4100px;height:56px;background:var(--bottom);color:#bbb;font-size:13px;text-align:center;line-height:56px}
</style>
</head>
<body>

<header class="site-header">
  <div class="brand"><span class="dot"></span>RIDGEFERN</div>
  <div class="contact-top">
    <span><svg width="14" height="14" viewBox="0 0 24 24"><path fill="#111" d="M6.6 10.8a15 15 0 006.6 6.6l2.2-2.2a1 1 0 011-.25 11 11 0 003.6.6 1 1 0 011 1V20a1 1 0 01-1 1A17 17 0 013 4a1 1 0 011-1h3.5a1 1 0 011 1 11 11 0 00.6 3.6 1 1 0 01-.25 1z"/></svg>(021) 555-0148</span>
    <span><svg width="16" height="12" viewBox="0 0 16 12"><rect width="16" height="12" fill="#111"/><path d="M0 0l8 6 8-6" stroke="#fff" fill="none"/></svg>hello@ridgefern.example</span>
  </div>
  <nav class="nav"><a class="active">About us</a><a>What we offer</a><a>Bookings/Contact</a></nav>
</header>

<section class="hero">
  <div class="photo" role="img" aria-label="Riders on electric mountain bikes on a hillside trail in the Nelson ranges"></div>
  <svg class="arrow-side" style="left:26px;top:270px" viewBox="0 0 30 50"><path d="M24 4L6 25l18 21" stroke="#fff" stroke-width="5" fill="none"/></svg>
  <svg class="arrow-side" style="right:26px;top:270px" viewBox="0 0 30 50"><path d="M6 4l18 21L6 46" stroke="#fff" stroke-width="5" fill="none"/></svg>
  <div class="content">
    <h1>RIDGEFERN</h1>
    <p>We are an Electric Mountain bike tour company in New Zealand.<br>We will be offering bike rental and guided tours around the Nelson region in New Zealand.</p>
    <span class="btn">READ MORE<span class="arr"><svg width="14" height="12" viewBox="0 0 14 12"><path d="M0 6h11M7 1l5 5-5 5" stroke="#fff" stroke-width="2" fill="none"/></svg></span></span>
  </div>
</section>

<section class="about">
  <h2 class="title">About <span class="light">Us</span></h2>
  <p class="subtitle">We are an Electric Mountain bike tour company in New Zealand.<br>We will be offering bike rental and guided tours around the Nelson region in New Zealand.</p>
  <div class="gallery">
    <div class="photo" role="img" aria-label="Group of riders with e-bikes on a forest trail" style="background:linear-gradient(160deg,#6f8a4e,#3c5a2e)"></div>
    <div class="photo" role="img" aria-label="Rider on a gravel track in the hills" style="background:linear-gradient(160deg,#8b8070,#5a5244)"></div>
    <div class="photo" role="img" aria-label="Rider descending a mountain track" style="background:linear-gradient(160deg,#7a6a5c,#3d3630)"></div>
  </div>
  <p class="lorem">Lorem ipsum dolor sit amet, consectetuer adipiscing elit. Aenean commodo ligula eget dolor. Aenean massa. Cum sociis natoque penatibus et magnis dis parturient montes, nascetur ridiculus mus. Donec quam felis, ultricies nec, pellentesque eu, pretium quis, sem. Nulla consequat massa quis enim. Donec pede justo, fringilla vel, aliquet nec, vulputate eget, arcu. In enim justo, rhoncus ut, imperdiet a, venenatis vitae, justo. Nullam dictum felis eu pede mollis pretium. Integer tincidunt. Cras dapibus. Vivamus elementum semper nisi.</p>
  <div class="center"><span class="btn">READ MORE<span class="arr"><svg width="14" height="12" viewBox="0 0 14 12"><path d="M0 6h11M7 1l5 5-5 5" stroke="#fff" stroke-width="2" fill="none"/></svg></span></span></div>
</section>

<section class="bike">
  <h2 class="title">Our Bike</h2>
  <p class="lorem">Lorem ipsum dolor sit amet, consectetuer adipiscing elit. Aenean commodo ligula eget dolor. Aenean massa. Cum sociis natoque penatibus et magnis dis parturient montes, nascetur ridiculus mus. Donec quam felis, ultricies nec, pellentesque eu, pretium quis, sem. Nulla consequat massa quis enim. Donec pede justo, fringilla vel, aliquet nec, vulputate eget, arcu. In enim justo, rhoncus ut, imperdiet a, venenatis vitae, justo. Nullam dictum felis eu pede mollis pretium. Integer tincidunt. Cras dapibus. Vivamus elementum semper nisi.</p>
  <div class="center"><span class="btn">READ MORE<span class="arr"><svg width="14" height="12" viewBox="0 0 14 12"><path d="M0 6h11M7 1l5 5-5 5" stroke="#fff" stroke-width="2" fill="none"/></svg></span></span></div>
</section>

<section class="offer">
  <div class="photo" role="img" aria-label="Dark background photo of riders on a mountain trail"></div>
  <h2 class="title">What we <span class="light">Offer</span></h2>
  <p class="intro">Lorem ipsum dolor sit amet, consectetuer adipiscing elit. Aenean commodo ligula eget dolor. Aenean massa. Cum sociis natoque penatibus et magnis dis parturient montes, nascetur ridiculus mus.</p>
  <svg class="arrow-side" style="left:40px;top:350px" viewBox="0 0 30 50"><path d="M24 4L6 25l18 21" stroke="#ddd" stroke-width="5" fill="none"/></svg>
  <svg class="arrow-side" style="right:40px;top:350px" viewBox="0 0 30 50"><path d="M6 4l18 21L6 46" stroke="#ddd" stroke-width="5" fill="none"/></svg>
  <div class="cards">
    <div class="card"><div class="photo" role="img" aria-label="Rider looking over a lake and hills" style="background:linear-gradient(180deg,#8fb0c8,#4e6e5a)"></div><h3>Bike rental &amp; pricing</h3><p>Lorem ipsum dolor sit amet, consectetuer adipiscing elit. Aenean commodo ligula eget dolor. Aenean massa cum sociis.</p><span class="btn">READ MORE<span class="arr"><svg width="14" height="12" viewBox="0 0 14 12"><path d="M0 6h11M7 1l5 5-5 5" stroke="#fff" stroke-width="2" fill="none"/></svg></span></span></div>
    <div class="card"><div class="photo" role="img" aria-label="Row of rental e-bikes parked outdoors" style="background:linear-gradient(180deg,#9aa0a4,#5a5e55)"></div><h3>Guided tours &amp; pricing</h3><p>Lorem ipsum dolor sit amet, consectetuer adipiscing elit. Aenean commodo ligula eget dolor. Aenean massa cum sociis.</p><span class="btn">READ MORE<span class="arr"><svg width="14" height="12" viewBox="0 0 14 12"><path d="M0 6h11M7 1l5 5-5 5" stroke="#fff" stroke-width="2" fill="none"/></svg></span></span></div>
    <div class="card"><div class="photo" role="img" aria-label="Riders on a forest track in sunlight" style="background:linear-gradient(180deg,#8fae5a,#3e5a2a)"></div><h3>Recommended package deals</h3><p>Lorem ipsum dolor sit amet, consectetuer adipiscing elit. Aenean commodo ligula eget dolor. Aenean massa cum sociis.</p><span class="btn">READ MORE<span class="arr"><svg width="14" height="12" viewBox="0 0 14 12"><path d="M0 6h11M7 1l5 5-5 5" stroke="#fff" stroke-width="2" fill="none"/></svg></span></span></div>
  </div>
</section>

<section class="blog">
  <h2 class="title">Latest Blog</h2>
  <svg class="arrow-side" style="left:40px;top:288px" viewBox="0 0 30 50"><path d="M24 4L6 25l18 21" stroke="#999" stroke-width="5" fill="none"/></svg>
  <svg class="arrow-side" style="right:40px;top:288px" viewBox="0 0 30 50"><path d="M6 4l18 21L6 46" stroke="#999" stroke-width="5" fill="none"/></svg>
  <div class="cards">
    <div class="card"><div class="photo" role="img" aria-label="Riders below snowy mountain peaks" style="background:linear-gradient(180deg,#b8cde0,#6d8aa3 45%,#5a6b3e)"></div><h3>Lorem ipsum dolor sit amet</h3><div class="date">October 22, 2017</div><p>Lorem ipsum dolor sit amet, consectetuer adipiscing elit. Aenean commodo ligula eget dolor massa.</p><span class="btn">READ MORE<span class="arr"><svg width="14" height="12" viewBox="0 0 14 12"><path d="M0 6h11M7 1l5 5-5 5" stroke="#fff" stroke-width="2" fill="none"/></svg></span></span></div>
    <div class="card"><div class="photo" role="img" aria-label="Rider on a sunlit woodland trail" style="background:linear-gradient(180deg,#d9b56a,#7a6a3a 50%,#3f3a22)"></div><h3>Lorem ipsum dolor sit amet</h3><div class="date">October 22, 2017</div><p>Lorem ipsum dolor sit amet, consectetuer adipiscing elit. Aenean commodo ligula eget dolor massa.</p><span class="btn">READ MORE<span class="arr"><svg width="14" height="12" viewBox="0 0 14 12"><path d="M0 6h11M7 1l5 5-5 5" stroke="#fff" stroke-width="2" fill="none"/></svg></span></span></div>
    <div class="card"><div class="photo" role="img" aria-label="Rider in green forest undergrowth" style="background:linear-gradient(180deg,#7da04a,#3a5a24)"></div><h3>Lorem ipsum dolor sit amet</h3><div class="date">October 22, 2017</div><p>Lorem ipsum dolor sit amet, consectetuer adipiscing elit. Aenean commodo ligula eget dolor massa.</p><span class="btn">READ MORE<span class="arr"><svg width="14" height="12" viewBox="0 0 14 12"><path d="M0 6h11M7 1l5 5-5 5" stroke="#fff" stroke-width="2" fill="none"/></svg></span></span></div>
  </div>
</section>

<section class="testi">
  <h2 class="t1">Client <span class="light">Testimonials</span></h2>
  <h2 class="t2">Featured <span class="light">Videos</span></h2>
  <div class="quote">
    <p>Lorem ipsum dolor sit amet, consectetuer adipiscing elit. Aenean commodo ligula eget dolor. Aenean massa. Cum sociis natoque penatibus et magnis dis parturient montes, nascetur ridiculus mus. Donec quam felis, ultricies nec, pellentesque eu, pretium quis, sem. Nulla consequat massa quis enim. Donec pede justo, fringilla vel, aliquet nec.</p>
    <span class="who">Aroha K.</span>
  </div>
  <div class="avatar" role="img" aria-label="Portrait of the client"></div>
  <div class="video">
    <div class="photo" role="img" aria-label="Video still of riders on a trail"></div>
    <svg style="position:absolute;left:178px;top:66px" width="44" height="44" viewBox="0 0 44 44"><circle cx="22" cy="22" r="21" fill="rgba(0,0,0,.45)" stroke="#fff" stroke-width="2"/><path d="M17 13l14 9-14 9z" fill="#fff"/></svg>
    <div class="bar">
      <svg width="400" height="26" viewBox="0 0 400 26"><path d="M10 7l9 6-9 6z" fill="#fff"/><rect x="30" y="12" width="300" height="3" fill="#777"/><rect x="30" y="12" width="90" height="3" fill="#3ea536"/><rect x="344" y="8" width="10" height="10" fill="#fff"/><rect x="368" y="8" width="16" height="10" fill="none" stroke="#fff" stroke-width="2"/></svg>
    </div>
  </div>
</section>

<section class="news">
  <div class="icon"><svg width="44" height="44" viewBox="0 0 44 44"><rect x="12" y="15" width="20" height="14" fill="#3ea536"/><path d="M12 15l10 8 10-8" stroke="#fff" stroke-width="1.5" fill="none"/></svg></div>
  <div class="label">News letter Signup</div>
  <div class="input">Enter your email</div>
  <div class="sub">SUBSCRIBE</div>
</section>

<footer class="site-footer">
  <div class="f-brand"><span class="dot"></span>RIDGEFERN</div>
  <div class="follow">FOLLOW US ON<div class="row"><i></i><i></i><i></i><i></i><i></i></div></div>
  <div class="contact-col f-col">
    <h4>Contact</h4>
    <p>12 Example Road, Stoke<br>Nelson 7011, New Zealand</p>
    <p class="item" style="margin-top:8px"><svg width="12" height="12" viewBox="0 0 24 24"><path fill="#3ea536" d="M6.6 10.8a15 15 0 006.6 6.6l2.2-2.2a1 1 0 011-.25 11 11 0 003.6.6 1 1 0 011 1V20a1 1 0 01-1 1A17 17 0 013 4a1 1 0 011-1h3.5a1 1 0 011 1 11 11 0 00.6 3.6 1 1 0 01-.25 1z"/></svg>(021) 555-0148</p>
    <p class="item"><svg width="12" height="10" viewBox="0 0 16 12"><rect width="16" height="12" fill="#3ea536"/><path d="M0 0l8 6 8-6" stroke="#0b0b0b" fill="none"/></svg>hello@ridgefern.example</p>
    <p class="item"><svg width="12" height="12" viewBox="0 0 12 12"><circle cx="6" cy="6" r="5" fill="none" stroke="#3ea536" stroke-width="1.5"/></svg>www.ridgefern.example</p>
    <h4 class="ql">QuickLinks</h4>
    <ul><li>About us</li><li>What we offer</li><li>Bookings/Contact</li></ul>
  </div>
  <div class="booking f-col">
    <h4>Booking</h4>
    <div class="form">
      <div class="field">First Name :</div><div class="field">LastName :</div>
      <div class="field">Phone No :</div><div class="field">Email Address :</div>
      <div class="field msg">Message :</div>
    </div>
    <span class="submit">Submit</span>
  </div>
</footer>

<div class="bottom" style="position:absolute;left:0;width:1200px">© 2017 RIDGEFERN &nbsp;•&nbsp; Privacy Policy &nbsp;|&nbsp; User Agreement</div>

</body>
</html>
```